Gutschein-Design für Verkauf von Online-Schmuckstücken
Zielgruppe
Wir verkaufen Online Schmuckstücke!
www.silberfaden-shop.de
Aufgabenstellung
Wir haben eine schwarze Schachtel erstellt und da drinne wird eine Geschenkgutschein sein:
Es soll sehr schlicht sein und schwarzen Hintergrund haben.
Vorderseite nur unser LOGO.
Rückseite:
Betrag: _________
Gültig Bis: _________
Code: __________
Und unten klein gedruckt steht:
Diese Karte ist gültig nur auf der online shop seite www.silberfaden-shop.de und in unserer offizielen Stores. Dieses Karte ist nicht gültig bei rabatierte Produkten und man kann nicht mit dieser karte einen Gutscheinkarte kaufen.
Der Design soll sehr schlicht und dezenz sein.

```html
<!DOCTYPE html>
<html lang="de">
<head>
<meta charset="utf-8">
<title>Silberfaden Gutscheinkarte</title>
<link href="https://fonts.googleapis.com/css2?family=Great+Vibes&family=Open+Sans:wght@400&display=swap" rel="stylesheet">
<style>
  :root {
    --ink: #0a0a0a;
    --paper: #ffffff;
    --backdrop: #e4e4e4;
    --field: #d2d2d2;
  }
  * { margin: 0; padding: 0; box-sizing: border-box; }
  html, body {
    width: 849px; height: 1200px; overflow: hidden;
    background: var(--backdrop);
    font-family: "Open Sans", sans-serif;
  }
  .sheet {
    width: 849px; height: 1200px;
    display: flex; flex-direction: column; align-items: center;
    justify-content: center; gap: 40px;
  }
  .card {
    position: relative;
    width: 560px; height: 560px;
  }
  .card__frame {
    position: absolute; inset: 15px;
  }
  /* Front */
  .card--front { background: var(--ink); }
  .card--front .card__frame { border: 1px solid var(--paper); }
  .brand {
    position: absolute; left: 0; right: 0; top: 236px;
    display: flex; flex-direction: column; align-items: center; gap: 14px;
  }
  .brand__dot {
    width: 56px; height: 56px; border-radius: 50%; background: var(--paper);
  }
  .brand__name {
    color: var(--paper); font-size: 30px; letter-spacing: 0.08em;
  }
  /* Back */
  .card--back { background: var(--paper); }
  .card--back .card__frame { border: 1px solid var(--ink); }
  .back__dot {
    position: absolute; left: 256px; top: 115px;
    width: 48px; height: 48px; border-radius: 50%; background: var(--ink);
  }
  .back__amount-label {
    position: absolute; left: 0; right: 0; top: 170px;
    text-align: center; font-family: "Great Vibes", cursive;
    font-size: 50px; color: var(--ink); line-height: 1;
  }
  .back__amount-field {
    position: absolute; left: 174px; top: 256px;
    width: 212px; height: 37px; background: var(--field);
  }
  .back__label {
    position: absolute; left: 0; right: 0;
    text-align: center; font-size: 10px; color: var(--ink);
  }
  .back__label--valid { top: 344px; }
  .back__label--code { top: 400px; }
  .back__line {
    position: absolute; left: 175px; width: 210px; height: 1px; background: var(--ink);
  }
  .back__line--valid { top: 383px; }
  .back__line--code { top: 440px; }
  .back__terms {
    position: absolute; left: 0; right: 0; top: 500px;
    text-align: center; font-size: 8px; line-height: 1.35; color: var(--ink);
  }
</style>
</head>
<body>
<main class="sheet">
  <section class="card card--front" aria-label="Vorderseite">
    <div class="card__frame"></div>
    <div class="brand">
      <span class="brand__dot"></span>
      <span class="brand__name">Silberfaden</span>
    </div>
  </section>

  <section class="card card--back" aria-label="Rückseite">
    <div class="card__frame"></div>
    <span class="back__dot"></span>
    <h1 class="back__amount-label">Betrag</h1>
    <div class="back__amount-field" role="img" aria-label="Feld für den Gutscheinbetrag"></div>
    <p class="back__label back__label--valid">Gültig bis</p>
    <div class="back__line back__line--valid"></div>
    <p class="back__label back__label--code">Code</p>
    <div class="back__line back__line--code"></div>
    <p class="back__terms">
      Diese Karte ist gültig in unserem Onlineshop: www.silberfaden-shop.de und in unseren offiziellen Stores.<br>
      Dieses Karte ist nicht einzulösen bei rabattierten Produkten und beim Kauf einer Gutscheinkarte.
    </p>
  </section>
</main>
</body>
</html>
```